Dental Practice Website design

Design a new website for Brambleford Dental Practice.
Design should be warm, neutral in colour, with some small amount of bright colour if needed but kept to a minimum. Website should look professional, high end. Home page should be easy to navigate and simple for patients to be able to book online.
Logo in files along with some examples of websites that we like. Please ask if any further info needed.
Menu should have:
About
New Patients
Treatments
Fees
Contact Us

Industry/Entity Type

Dentistry

Number of Pages Required

4 page

Font styles to use
Sans Serif

Colors

Designer to choose colors to be used in the design.

Requirements
Must have
• Ravelle ratings badge, book online button,
Nice to have
• neutral, relaxing colours
Should not have
• harsh, bright colours!

```html
<!DOCTYPE html>
<html lang="en">
<head>
<meta charset="utf-8">
<title>Brambleford Dental Practice</title>
<link href="https://fonts.googleapis.com/css2?family=Lato:wght@400;700;900&display=swap" rel="stylesheet">
<style>
:root{
  --dark:#1b2a2e;
  --gold:#8b7648;
  --gold-soft:rgba(139,118,72,.92);
  --sand:#f1efeb;
  --ink:#1e2a2d;
  --muted:#5d5d5d;
  --white:#ffffff;
}
*{box-sizing:border-box;margin:0;padding:0}
html,body{width:1200px;height:4179px;overflow:hidden}
body{font-family:'Lato',sans-serif;color:var(--ink);background:var(--white);position:relative}
.abs{position:absolute}
.btn{position:absolute;background:var(--gold);color:var(--white);font-size:15px;display:flex;align-items:center;justify-content:center;border-radius:2px}
.btn.dark{background:var(--dark)}
.heading{font-weight:700;font-size:39px;color:var(--ink)}
.heading span{color:var(--gold)}
.underline{position:absolute;height:4px;background:var(--gold);width:88px}
.photo{position:absolute}

/* top */
.topbar{left:0;top:0;width:1200px;height:42px;background:var(--dark);color:var(--white);font-size:13px}
.topbar .item{position:absolute;top:13px;display:flex;align-items:center;gap:7px}
.nav{left:0;top:42px;width:1200px;height:81px;background:var(--white)}
.nav a{position:absolute;top:28px;font-size:15px;color:#333;text-decoration:none}
.nav a.active{background:var(--dark);color:var(--white);font-weight:700;padding:4px 10px;top:25px;border-radius:2px}
.logo{left:112px;top:0;width:243px;height:172px;background:var(--dark);border-radius:0 0 18px 18px;color:var(--white);text-align:center;z-index:5;overflow:hidden}
.logo .mark{position:absolute;left:66px;top:22px;width:110px;height:64px;border:2px solid #d9d9d9}
.logo .name{position:absolute;left:0;right:0;top:98px;font-size:27px;letter-spacing:1px;font-weight:400;line-height:32px;white-space:nowrap}
.logo .sub{position:absolute;left:0;right:0;top:134px;font-size:17px;letter-spacing:1.5px;font-weight:400;line-height:20px;white-space:nowrap}

/* hero */
.hero{left:0;top:123px;width:1200px;height:600px;background:linear-gradient(100deg,#6f7274 0%,#8a8c8d 40%,#7b8186 70%,#56657a 100%)}
.hero h1{position:absolute;left:0;right:0;top:152px;text-align:center;color:var(--white);font-size:60px;font-weight:900;line-height:75px;letter-spacing:-.5px}
.hero p{position:absolute;left:0;right:0;top:312px;text-align:center;color:var(--white);font-size:25px;line-height:35px}
.arrow{position:absolute;top:273px;width:38px;height:38px;background:var(--dark);display:flex;align-items:center;justify-content:center}

/* about */
.about-text{left:637px;top:900px;width:450px;font-size:14.5px;line-height:24px;color:var(--muted)}
.about-text p+p{margin-top:24px}

/* treatments */
.card-title{position:absolute;text-align:center;font-size:23px;font-weight:700;color:var(--ink)}
.card-text{position:absolute;text-align:center;font-size:14.5px;line-height:23px;color:var(--muted)}

/* team */
.team-box{left:110px;top:2014px;width:635px;height:408px;background:var(--gold-soft)}
.team-box h2{position:absolute;left:65px;top:40px;color:var(--white);font-size:39px;font-weight:700}
.team-box .bar{position:absolute;left:65px;top:100px;width:88px;height:3px;background:var(--white)}
.team-box p{position:absolute;left:65px;top:124px;width:520px;color:var(--white);font-size:14.5px;line-height:24px}

/* join */
.join{left:0;top:2496px;width:1200px;height:529px;background:var(--sand)}
.join p{position:absolute;left:220px;width:760px;text-align:center;font-size:14.5px;line-height:26px;color:var(--muted)}

/* why */
.why-card{position:absolute;top:3252px;width:228px;height:218px;background:#e8e8e6;text-align:center;padding:0 16px}
.why-card.on{background:var(--dark)}
.why-card svg{margin-top:16px}
.why-card h3{font-size:17px;font-weight:700;line-height:23px;margin-top:8px;color:var(--ink)}
.why-card.on h3{color:var(--gold)}
.why-card p{font-size:14.5px;line-height:21px;color:var(--muted);margin-top:8px}
.why-card.on p{color:var(--white)}

/* testimonial + footer */
.footer-band{left:0;top:3653px;width:1200px;height:526px;background:var(--dark)}
.quote-box{left:112px;top:3556px;width:976px;height:235px;background:linear-gradient(90deg,#8b7648 0%,#8b7648 58%,#a49573 78%,#c8c3b6 100%)}
.quote-box p{position:absolute;left:84px;top:58px;width:530px;color:var(--white);font-size:16px;line-height:28px}
.quote-box .who{position:absolute;left:84px;top:175px;color:var(--white);font-size:21px;font-weight:700}
.dots{position:absolute;left:450px;top:183px;display:flex;gap:10px}
.dots i{display:block;width:19px;height:5px;background:var(--white)}
.badge{left:925px;top:3739px;width:141px;height:68px;background:var(--white);border-radius:6px;box-shadow:0 2px 6px rgba(0,0,0,.2)}
.f-title{position:absolute;top:3856px;color:var(--white);font-size:21px;font-weight:700}
.f-text{position:absolute;color:var(--white);font-size:14.5px;line-height:26px}
.f-list{position:absolute;top:3902px;list-style:none;color:var(--white);font-size:15px}
.f-list li{height:38.5px}
.contact-row{position:absolute;left:436px;display:flex;gap:20px;color:var(--white);font-size:14.5px;line-height:24px}
.social{position:absolute;top:4030px;left:112px;display:flex;gap:10px;align-items:center}
.social span{color:var(--white);font-size:13px;display:flex;align-items:center;gap:5px}
.social span b{display:inline-block;width:10px;height:10px;border-radius:50%;background:var(--gold)}
.rule{left:112px;top:4131px;width:976px;height:1px;background:#3a4a4e}
.copy{left:0;right:0;top:4146px;text-align:center;color:var(--white);font-size:12.5px}
</style>
</head>
<body>

<div class="abs topbar">
  <div class="item" style="left:607px">
    <svg width="13" height="13" viewBox="0 0 24 24"><rect x="1" y="1" width="22" height="22" rx="4" fill="#fff"/><path d="M8 5l2 4-2 2a11 11 0 005 5l2-2 4 2-1 3c-7 0-13-6-13-13z" fill="#1b2a2e"/></svg>
    Call Us : +1 555 014 2290
  </div>
  <div class="item" style="left:818px">
    <svg width="15" height="11" viewBox="0 0 24 18"><rect width="24" height="18" rx="2" fill="#fff"/><path d="M1 2l11 8 11-8" stroke="#1b2a2e" stroke-width="2" fill="none"/></svg>
    Email : info@bramblefordental.com
  </div>
</div>

<div class="abs nav">
  <a class="active" style="left:526px">Home</a>
  <a style="left:616px">About</a>
  <a style="left:697px">New Patients</a>
  <a style="left:826px">Treatments</a>
  <a style="left:942px">Fees</a>
  <a style="left:1011px">Contact Us</a>
</div>

<section class="abs hero" role="img" aria-label="Dentist at a desk with keyboard and dental instruments">
  <h1>CARING FOR YOUR SMILE,<br>ONE VISIT AT A TIME</h1>
  <p>Providing high-quality, patient-focused dentistry<br>with a gentle touch.</p>
  <div class="btn" style="left:523px;top:412px;width:154px;height:40px;font-weight:700">Book Online</div>
  <div class="arrow" style="left:36px"><svg width="12" height="16" viewBox="0 0 12 16"><path d="M9 1L2 8l7 7" stroke="#fff" stroke-width="1.6" fill="none"/></svg></div>
  <div class="arrow" style="left:1126px"><svg width="12" height="16" viewBox="0 0 12 16"><path d="M3 1l7 7-7 7" stroke="#fff" stroke-width="1.6" fill="none"/></svg></div>
</section>

<div class="abs logo">
  <div class="mark"></div>
  <div class="name">BRAMBLEFORD</div>
  <div class="sub">DENTAL PRACTICE</div>
</div>

<div class="photo" style="left:112px;top:809px;width:454px;height:459px;background:linear-gradient(135deg,#c9cdd2,#8f9aa4 60%,#6e7a85)" role="img" aria-label="Patient smiling in a hand mirror during a dental check"></div>
<h2 class="abs heading" style="left:637px;top:812px">About <span>Us</span></h2>
<div class="underline" style="left:637px;top:862px"></div>
<div class="abs about-text">
  <p>Welcome to our friendly dental practice nestled in the heart of beautiful Hollowmere, UK. Our team of dedicated dentists, hygienists and support staff are here to provide you with exceptional dental care. With a wide array of services, including general and cosmetic dentistry, orthodontics and emergency care, we're confident that we can deliver the highest quality treatment to you and your loved ones.</p>
  <p>At our practice, we believe that a visit to the dentist should be a comfortable and positive experience. We strive to create a warm and welcoming atmosphere where our patients can feel at ease and confident in the care they receive.</p>
</div>
<div class="btn" style="left:637px;top:1217px;width:146px;height:37px">Read More</div>

<h2 class="abs heading" style="left:0;right:0;top:1342px;text-align:center">Our <span>Treatments</span></h2>
<div class="underline" style="left:540px;top:1392px;width:190px"></div>

<div class="photo" style="left:112px;top:1429px;width:303px;height:242px;background:linear-gradient(135deg,#a9b4bc,#7b8c99)" role="img" aria-label="Patient in protective glasses during cosmetic treatment"></div>
<div class="photo" style="left:449px;top:1429px;width:303px;height:242px;background:linear-gradient(135deg,#c89a86,#a86f62)" role="img" aria-label="Clear orthodontic aligner held near a smile"></div>
<div class="photo" style="left:785px;top:1429px;width:303px;height:242px;background:linear-gradient(135deg,#d6dde3,#7ea0b8)" role="img" aria-label="Dental team with a patient in the treatment room"></div>

<div class="card-title" style="left:112px;width:303px;top:1686px">Cosmetic Dentistry</div>
<div class="card-title" style="left:449px;width:303px;top:1686px">Orthodontics</div>
<div class="card-title" style="left:785px;width:303px;top:1686px">Emergency Care</div>
<div class="card-text" style="left:122px;width:283px;top:1726px">Excepteur sint occaecat cupidatat non proident, sunt in culpa qui officia deser mollit anim id est laborum.</div>
<div class="card-text" style="left:459px;width:283px;top:1726px">Excepteur sint occaecat cupidatat non proident, sunt in culpa qui officia deser mollit anim id est laborum.</div>
<div class="card-text" style="left:795px;width:283px;top:1726px">Excepteur sint occaecat cupidatat non proident, sunt in culpa qui officia deser mollit anim id est laborum.</div>
<div class="btn" style="left:191px;top:1815px;width:146px;height:37px">Read More</div>
<div class="btn" style="left:528px;top:1815px;width:146px;height:37px">Read More</div>
<div class="btn" style="left:864px;top:1815px;width:146px;height:37px">Read More</div>

<div class="abs" style="left:0;top:1940px;width:600px;height:556px;background:var(--dark)"></div>
<div class="photo" style="left:600px;top:1940px;width:600px;height:556px;background:linear-gradient(135deg,#7fa8d6,#2f69b8 55%,#1f4f96)" role="img" aria-label="Smiling dental team in blue scrubs"></div>
<div class="abs team-box">
  <h2>Our Team</h2>
  <div class="bar"></div>
  <p>We are delighted to introduce you to our experienced and compassionate dental team. Our team comprises highly skilled dental professionals who are dedicated to providing you with high-quality dental care services. Led by our experienced dentist, each member of our team brings their own unique set of skills and expertise. From our friendly reception staff to our knowledgeable hygienists and assistants, our team is here to ensure that you receive personalised dental care that meets your unique needs and preferences.</p>
  <div class="btn dark" style="left:65px;top:321px;width:146px;height:37px">Read More</div>
</div>

<section class="abs join">
  <h2 class="heading" style="position:absolute;left:0;right:0;top:80px;text-align:center">Join Our <span>Practice</span></h2>
  <div class="underline" style="left:560px;top:130px;width:120px"></div>
  <p style="top:158px">If you're looking for an exceptional dental practice, we're here to help! Our team is made up of highly skilled professionals who are dedicated to ensuring that all our patients receive top-notch care in a welcoming and comfortable environment. Whether you need a routine examination or a more specialised treatment, we have all the resources to provide you with the best dental care possible. Our practice is always up-to-date with the latest techniques and technologies to make sure that our patients receive the best possible results.</p>
  <p style="top:306px">We understand that dental care can be expensive which is why we offer affordable prices to ensure that everyone has access to quality care. If you'd like to learn more about our practice, please don't hesitate to contact us.</p>
  <div class="btn" style="left:460px;top:404px;width:281px;height:38px">Book Your Appointment online!</div>
</section>

<h2 class="abs heading" style="left:0;right:0;top:3100px;text-align:center">Why <span>Choose Us?</span></h2>
<div class="underline" style="left:548px;top:3150px;width:190px"></div>
<p class="abs" style="left:290px;width:620px;top:3182px;text-align:center;font-size:14.5px;line-height:23px;color:var(--muted)">At Brambleford Dental Practice, we believe in providing exceptional dental care in a warm and welcoming environment. Here's why patients trust us with their smiles:</p>

<div class="why-card" style="left:112px">
  <svg width="60" height="56" viewBox="0 0 60 56" fill="none" stroke="#8b7648" stroke-width="1.6"><path d="M14 8c6-4 10 0 14 0s8-4 14 0 4 16 0 22-4 20-8 20-4-14-6-14-2 14-6 14-4-14-8-20-6-18 0-22z"/><path d="M40 26l10 4v8c0 6-5 9-10 11-5-2-10-5-10-11v-8z"/><path d="M36 37l3 3 6-6"/></svg>
  <h3>Comprehensive Dental Services</h3>
  <p>Excepteur sint occaecat cupidatat non proident, sunt culpa qui officia aborum.</p>
</div>
<div class="why-card" style="left:362px">
  <svg width="72" height="56" viewBox="0 0 72 56" fill="none" stroke="#8b7648" stroke-width="1.6"><circle cx="36" cy="16" r="8"/><circle cx="16" cy="22" r="6"/><circle cx="56" cy="22" r="6"/><path d="M22 46c0-10 6-16 14-16s14 6 14 16z"/><path d="M4 46c0-8 5-12 12-12 3 0 5 1 7 2"/><path d="M68 46c0-8-5-12-12-12-3 0-5 1-7 2"/></svg>
  <h3>Experienced &amp; Friendly Team</h3>
  <p>Excepteur sint occaecat cupidatat non proident, sunt culpa qui officia aborum.</p>
</div>
<div class="why-card on" style="left:611px">
  <svg width="64" height="56" viewBox="0 0 64 56" fill="none" stroke="#8b7648" stroke-width="1.6"><circle cx="38" cy="14" r="10"/><path d="M38 8v12M35 11h5a2 2 0 010 4h-4a2 2 0 000 4h5"/><path d="M4 40l10-8h14l8 4H24M14 48l8-4h18l18-12"/></svg>
  <h3>Affordable &amp; Transparent Pricing</h3>
  <p>Excepteur sint occaecat cupidatat non proident, sunt culpa qui officia aborum.</p>
</div>
<div class="why-card" style="left:861px">
  <svg width="64" height="56" viewBox="0 0 64 56" fill="none" stroke="#8b7648" stroke-width="1.6"><path d="M32 4l12 5v9c0 7-6 11-12 13-6-2-12-6-12-13V9z"/><circle cx="22" cy="36" r="8"/><circle cx="22" cy="36" r="3"/><rect x="36" y="32" width="16" height="14" rx="2"/><path d="M28 12l3 3 6-6"/></svg>
  <h3>State-of-the-Art Technology</h3>
  <p>Excepteur sint occaecat cupidatat non proident, sunt culpa qui officia aborum.</p>
</div>

<div class="abs footer-band"></div>
<div class="abs quote-box" role="img" aria-label="Smiling patient portrait beside testimonial">
  <svg class="abs" style="left:47px;top:44px" width="30" height="22" viewBox="0 0 30 22"><path d="M0 22V12C0 5 4 1 11 0v4c-4 1-5 4-5 7h5v11zM17 22V12c0-7 4-11 11-12v4c-4 1-5 4-5 7h5v11z" fill="#fff"/></svg>
  <p>Lorem ipsum dolor sit amet, consectetur adipiscing elit, sed do eiusmod tempor incididunt ut labore et dolore magna aliqua. Ut enim ad minim veniam, quis nostrud exercitation ullamco laboris nisi ut aliquip ex ea commodo consequat.</p>
  <div class="who">R. Penrose</div>
  <div class="dots"><i></i><i></i><i></i></div>
</div>
<div class="abs badge" role="img" aria-label="Ravelle ratings badge"></div>

<div class="f-title" style="left:112px">About Us</div>
<div class="f-text" style="left:112px;top:3898px;width:260px">Our team of dedicated dentists, hygienists and support staff are here to provide you with exceptional dental care.</div>
<div class="social">
  <span><b></b>Chirpa</span><span><b></b>Lenspot</span><span><b></b>Workly</span><span><b></b>Vidstream</span>
</div>

<div class="f-title" style="left:436px">Contact Us</div>
<div class="contact-row" style="top:3902px">
  <svg width="18" height="24" viewBox="0 0 18 24" fill="none" stroke="#fff" stroke-width="1.4"><path d="M9 23s8-8 8-14A8 8 0 001 9c0 6 8 14 8 14z"/><circle cx="9" cy="9" r="3"/></svg>
  <div>123, Brambleford Dental Practice<br>company Na 123456.</div>
</div>
<div class="contact-row" style="top:3985px">
  <svg width="18" height="18" viewBox="0 0 24 24" fill="none" stroke="#fff" stroke-width="1.6"><path d="M5 2l4 5-2 3a13 13 0 007 7l3-2 5 4-2 3C10 22 2 14 2 4z"/></svg>
  <div>+1 555 014 2290</div>
</div>
<div class="contact-row" style="top:4045px">
  <svg width="18" height="14" viewBox="0 0 24 18" fill="none" stroke="#fff" stroke-width="1.6"><rect x="1" y="1" width="22" height="16" rx="1"/><path d="M1 2l11 8 11-8"/></svg>
  <div>info@bramblefordental.com</div>
</div>

<div class="f-title" style="left:777px">Quick Links</div>
<ul class="f-list" style="left:777px"><li>Home</li><li>About</li><li>New Patients</li><li>Treatments</li><li>Fees</li></ul>
<div class="f-title" style="left:980px">Other Links</div>
<ul class="f-list" style="left:980px"><li>Contact Us</li><li>Team</li><li>Practice</li><li>Blog</li><li>Security</li></ul>

<div class="abs rule"></div>
<div class="abs copy">Copyright © 2025 Brambleford Dental Practice. All Rights Reserved</div>

</body>
</html>
```